RTavenor Business Cards & Letterhead

I have a logo but need a design for some new business cards. We are a Design-Build Firm that specializes in the design and construction of commercial projects.
the cards need to be professional. no cartoon stuff.
i would like to have the cards in AI format so I can update the card as needed. Logo is provided.
Our Address is: 4187 Marlowe Ct. Larkspur, Ohio 27614

```html
<!DOCTYPE html>
<html lang="en">
<head>
<meta charset="UTF-8">
<title>RTavenor Business Card</title>
<link href="https://fonts.googleapis.com/css2?family=Montserrat:wght@800&family=Arimo:wght@400;700&display=swap" rel="stylesheet">
<style>
  :root {
    --backdrop: #e4e4e2;
    --card-dark: #303031;
    --card-deep: #232324;
    --brand-blue: #0a6fb8;
    --brand-blue-deep: #0a4f8c;
    --text-light: #f4f4f4;
    --rule: #cfcfcf;
    --pattern-light: #4a4a4b;
  }
  * { margin: 0; padding: 0; box-sizing: border-box; }
  html, body { width: 1200px; height: 801px; overflow: hidden; }
  body {
    background: var(--backdrop);
    font-family: "Arimo", Arial, sans-serif;
    position: relative;
  }
  .card {
    position: absolute;
    top: 252px;
    width: 520px;
    height: 297px;
    background: var(--card-dark);
    overflow: hidden;
  }
  .card--front { left: 60px; }
  .card--back { left: 620px; }

  .wordmark {
    display: flex;
    align-items: center;
    gap: 10px;
    font-family: "Montserrat", Arial, sans-serif;
    font-weight: 800;
    color: var(--text-light);
    letter-spacing: 0.5px;
    white-space: nowrap;
  }
  .wordmark__square { background: var(--brand-blue); flex: none; }
  .card--front .wordmark { position: absolute; left: 34px; top: 36px; font-size: 30px; }
  .card--front .wordmark__square { width: 24px; height: 24px; }

  .holder { position: absolute; left: 62px; top: 96px; }
  .holder__name {
    font-weight: 700;
    font-size: 19px;
    color: var(--brand-blue);
    letter-spacing: 0.4px;
  }
  .holder__role { font-size: 13px; color: var(--text-light); margin-top: 2px; }

  .contacts {
    position: absolute;
    left: 62px;
    top: 160px;
    list-style: none;
  }
  .contacts__item {
    display: flex;
    align-items: center;
    gap: 8px;
    font-size: 13.5px;
    color: var(--text-light);
    line-height: 22px;
  }
  .contacts__icon { width: 12px; height: 12px; flex: none; }

  .card__rule {
    position: absolute;
    left: 62px;
    right: 40px;
    top: 236px;
    height: 1px;
    background: var(--rule);
  }
  .card__address {
    position: absolute;
    left: 62px;
    top: 244px;
    font-size: 14px;
    color: var(--text-light);
    letter-spacing: 0.2px;
    white-space: nowrap;
  }
  .edge-band {
    position: absolute;
    left: 60px;
    right: 0;
    bottom: 0;
    height: 9px;
    background: linear-gradient(90deg, var(--brand-blue-deep), var(--brand-blue));
  }
  .edge-tab {
    position: absolute;
    left: 0;
    width: 60px;
    bottom: 0;
    height: 9px;
    background: #ffffff;
  }
  .edge-mark {
    position: absolute;
    left: 0;
    bottom: 60px;
    width: 6px;
    height: 30px;
    background: var(--brand-blue);
  }

  .pattern-field {
    position: absolute;
    inset: 0;
    background: linear-gradient(120deg, var(--card-deep) 0%, var(--card-dark) 55%, var(--pattern-light) 100%);
  }
  .card--back .wordmark {
    position: absolute;
    left: 50%;
    top: 50%;
    transform: translate(-50%, -50%);
    font-size: 40px;
  }
  .card--back .wordmark__square { width: 32px; height: 32px; }
</style>
</head>
<body>
  <section class="card card--front">
    <div class="wordmark"><span class="wordmark__square"></span><span>RTAVENOR</span></div>
    <div class="holder">
      <p class="holder__name">MARCUS ELLERY</p>
      <p class="holder__role">Manager</p>
    </div>
    <ul class="contacts">
      <li class="contacts__item">
        <svg class="contacts__icon" viewBox="0 0 12 12"><path d="M2.5 1h2l1 3-1.4 1a6 6 0 0 0 2.9 2.9l1-1.4 3 1v2c0 .6-.4 1-1 1A9.5 9.5 0 0 1 1.5 2c0-.6.4-1 1-1z" fill="#cfcfcf"/></svg>
        <span>919-555-0148</span>
      </li>
      <li class="contacts__item">
        <svg class="contacts__icon" viewBox="0 0 12 12"><rect x="0.8" y="2.3" width="10.4" height="7.4" fill="none" stroke="#cfcfcf" stroke-width="1.1"/><path d="M1 2.6l5 4 5-4" fill="none" stroke="#cfcfcf" stroke-width="1.1"/></svg>
        <span>mellery@rtavenor.com</span>
      </li>
      <li class="contacts__item">
        <svg class="contacts__icon" viewBox="0 0 12 12"><circle cx="6" cy="6" r="5" fill="none" stroke="#cfcfcf" stroke-width="1.1"/><path d="M1 6h10M6 1c-2.5 2.8-2.5 7.2 0 10M6 1c2.5 2.8 2.5 7.2 0 10" fill="none" stroke="#cfcfcf" stroke-width="0.9"/></svg>
        <span>www.rtavenorbuild.com</span>
      </li>
    </ul>
    <div class="card__rule"></div>
    <p class="card__address">4187 Marlowe Ct. Larkspur, Ohio 27614</p>
    <div class="edge-mark"></div>
    <div class="edge-tab"></div>
    <div class="edge-band"></div>
  </section>

  <section class="card card--back">
    <div class="pattern-field" role="img" aria-label="Embossed repeating brand pattern in dark and mid grey"></div>
    <div class="wordmark"><span class="wordmark__square"></span><span>RTAVENOR</span></div>
  </section>
</body>
</html>
```